Financial Advisor Resource Firm needs business card design

Need business card design for company in Omaha NE called Meridale Circle. We provide resources to financial advisors....workshop programs, retirement analysis, and insurance planning. I would like to see designs that use grays, greens, black, and white colors. The final design should communicate 'collaboration' and be simple yet attractive to financial planning clients. I will attached our logo and another picture of a puzzle piece coming together. I would like the incorporate the puzzle picture somehow, maybe on the back somehow, with color or just the gray scale....OR, the picture be the front of the card with 'Meridale' definition on it (see upload) and then company logo, employee name, title, address on the back (see ppt uploaded). The following disclosure needs to be included somewhere- Advisory services offered through Stonebrook Assets, LLC.
Updates

I uploaded a svg and ai file of the logo

Target Market(s)

Financial planning clients and financial advisors....so pretty diverse age range of about 40-70.

Industry/Entity Type

Financial Planning

Contact Information for Business Card

Tobias L. Fenwright, MBA
Founder/President
5287 E. Larkin Road
Suite 230
Omaha, NE 68190
Phone- (402) 555-0147
Cell- (402) 555-0183
Fax- (402) 555-0129
email- tobias@meridaleplan.example
web address- www.meridaleplan.example

Colors
1b1b1b
474747
d3d3d3
ffffff
9bcb3c
abd036

Requirements
Must have
• Must include logo provided, must be 2 sided, and must have disclosure...all of these items listed in project description

```html
<!DOCTYPE html>
<html lang="en">
<head>
<meta charset="utf-8">
<title>Meridale Circle – Business Card</title>
<link rel="stylesheet" href="https://fonts.googleapis.com/css2?family=Cinzel:wght@400&family=Open+Sans:wght@400;600&family=Roboto+Condensed:wght@400;700&display=swap">
<style>
  :root {
    --ink: #1b1b1b;
    --charcoal: #474747;
    --mist: #d3d3d3;
    --paper: #ffffff;
    --leaf: #9bcb3c;
    --lime: #abd036;
    --backdrop: #e4e4e4;
    --card-stock: #f4f4f2;
  }
  * { box-sizing: border-box; margin: 0; padding: 0; }
  html, body { width: 1200px; height: 900px; overflow: hidden; }
  body {
    background: var(--backdrop);
    font-family: "Open Sans", sans-serif;
    color: var(--ink);
    position: relative;
  }
  .card {
    position: absolute;
    left: 250px;
    width: 700px;
    height: 400px;
    overflow: hidden;
    box-shadow: 0 4px 14px rgba(0,0,0,.18);
  }

  /* Front */
  .card-front { top: 36px; background: var(--paper); }
  .photo-area {
    position: absolute; top: 0; left: 0; right: 0; height: 228px;
    background: linear-gradient(135deg, #8a8a8a 0%, #5a5a5a 45%, #b5b5b5 70%, #6a6a6a 100%);
  }
  .word-band {
    position: absolute; top: 228px; left: 0; right: 0; height: 104px;
    background: var(--leaf);
  }
  .word {
    position: absolute; top: 8px; left: 0; right: 0; text-align: center;
    font-family: "Cinzel", serif; font-size: 50px; line-height: 60px;
    letter-spacing: 22px; color: var(--ink);
  }
  .pronunciation {
    position: absolute; top: 68px; left: 0; right: 0; text-align: center;
    font-size: 22px; line-height: 28px; color: var(--ink);
  }
  .definition-band {
    position: absolute; top: 332px; left: 0; right: 0; bottom: 0;
    background: var(--ink);
    display: flex; align-items: center; justify-content: center;
  }
  .definition { color: var(--paper); font-size: 19px; }

  /* Back */
  .card-back { top: 464px; background: var(--card-stock); }
  .brand {
    position: absolute; top: 22px; left: 0; right: 0; height: 46px;
    display: flex; justify-content: center; align-items: center; gap: 12px;
  }
  .brand-dot { width: 22px; height: 22px; border-radius: 50%; background: var(--leaf); }
  .brand-name { font-size: 34px; line-height: 46px; font-weight: 600; color: var(--ink); letter-spacing: 1px; }
  .rule { position: absolute; left: 40px; right: 40px; height: 1px; background: var(--ink); }
  .rule-brand { top: 78px; }
  .rule-disclosure { top: 116px; }
  .rule-contacts { top: 300px; }
  .rule-website { top: 348px; }
  .disclosure {
    position: absolute; top: 85px; left: 0; right: 0; text-align: center;
    font-size: 17px; line-height: 24px; color: var(--ink);
  }
  .person { position: absolute; top: 124px; left: 0; right: 0; text-align: center; }
  .person-name {
    font-family: "Roboto Condensed", sans-serif; font-weight: 700; font-size: 26px; line-height: 32px;
  }
  .person-title {
    font-family: "Roboto Condensed", sans-serif; font-size: 15px; line-height: 20px; letter-spacing: 3px;
  }
  .contact {
    position: absolute; font-family: "Roboto Condensed", sans-serif; font-size: 17px; line-height: 28px;
  }
  .contact-left { top: 200px; left: 60px; }
  .contact-right { top: 200px; right: 60px; text-align: right; }
  .contact-row { display: flex; align-items: center; gap: 12px; }
  .contact-right .contact-row { justify-content: flex-end; }
  .icon { width: 18px; height: 18px; fill: var(--ink); flex: none; }
  .address { line-height: 22px; }
  .divider { position: absolute; top: 196px; left: 370px; width: 1px; height: 92px; background: var(--ink); }
  .website {
    position: absolute; top: 312px; left: 0; right: 0; text-align: center;
    font-family: "Roboto Condensed", sans-serif; font-size: 18px; line-height: 26px;
  }
</style>
</head>
<body>

<section class="card card-front" aria-label="Card front">
  <div class="photo-area" role="img" aria-label="Grayscale photo of several hands joining puzzle pieces together"></div>
  <div class="word-band">
    <div class="word">MER·I·DALE</div>
    <div class="pronunciation">ˈmer·ə·dāl</div>
  </div>
  <div class="definition-band">
    <p class="definition">: to come together and unite in common interest and focus</p>
  </div>
</section>

<section class="card card-back" aria-label="Card back">
  <div class="brand">
    <span class="brand-dot"></span>
    <span class="brand-name">Meridale Circle</span>
  </div>
  <div class="rule rule-brand"></div>
  <p class="disclosure">Advisory services offered through Stonebrook Assets, LLC.</p>
  <div class="rule rule-disclosure"></div>

  <div class="person">
    <div class="person-name">Tobias L. Fenwright, MBA</div>
    <div class="person-title">FOUNDER/PRESIDENT</div>
  </div>

  <div class="contact contact-left">
    <div class="contact-row">
      <svg class="icon" viewBox="0 0 24 24"><path d="M6.6 10.8a15 15 0 0 0 6.6 6.6l2.2-2.2a1 1 0 0 1 1-.25 11.4 11.4 0 0 0 3.6.57 1 1 0 0 1 1 1V20a1 1 0 0 1-1 1A17 17 0 0 1 3 4a1 1 0 0 1 1-1h3.5a1 1 0 0 1 1 1c0 1.25.2 2.45.57 3.57a1 1 0 0 1-.25 1z"/></svg>
      <span>(402) 555-0147</span>
    </div>
    <div class="contact-row">
      <svg class="icon" viewBox="0 0 24 24"><path d="M7 1h10a2 2 0 0 1 2 2v18a2 2 0 0 1-2 2H7a2 2 0 0 1-2-2V3a2 2 0 0 1 2-2zm0 3v14h10V4zm5 15.5a1 1 0 1 0 0 2 1 1 0 0 0 0-2z"/></svg>
      <span>(402) 555-0183</span>
    </div>
    <div class="contact-row">
      <svg class="icon" viewBox="0 0 24 24"><path d="M2 5h20v14H2zm2 2v.5l8 5.5 8-5.5V7zm0 3v7h16v-7l-8 5.5z"/></svg>
      <span>tobias@meridaleplan.example</span>
    </div>
  </div>

  <div class="divider"></div>

  <div class="contact contact-right">
    <div class="contact-row">
      <span>(402) 555-0129</span>
      <svg class="icon" viewBox="0 0 24 24"><path d="M6 2h10v6H6zM3 9h18v13H3zm3 3v2h2v-2zm4 0v2h2v-2zm4 0v2h2v-2zm-8 4v2h2v-2zm4 0v2h2v-2zm4 0v2h2v-2z"/></svg>
    </div>
    <div class="contact-row">
      <span class="address">5287 E. Larkin Road • Suite 230<br>Omaha, NE 68190</span>
      <svg class="icon" viewBox="0 0 24 24"><path d="M12 2a7 7 0 0 1 7 7c0 5-7 13-7 13S5 14 5 9a7 7 0 0 1 7-7zm0 4a3 3 0 1 0 0 6 3 3 0 0 0 0-6z"/></svg>
    </div>
  </div>

  <div class="rule rule-contacts"></div>
  <p class="website">www.meridaleplan.example</p>
  <div class="rule rule-website"></div>
</section>

</body>
</html>
```